Business Card & Letterhead Design

We a financial advice company based in Australia. We provide advice to wealthy farmers.

We are changing our business name FROM Brightvale Financial TO Tallowmere Wealth and we need a new letterhead and double sided business card design

Attached is designs from our previous branding (Brightvale Financial) as it includes all the details we require on the new Tallowmere Wealth business cards and letterhead.

Need extra days to review

```html
<!DOCTYPE html>
<html lang="en">
<head>
<meta charset="utf-8">
<title>Tallowmere Wealth – Business Card</title>
<link rel="stylesheet" href="https://fonts.googleapis.com/css2?family=Cinzel:wght@700&family=Montserrat:wght@700&family=Oswald:wght@500&family=Yellowtail&family=Pompiere&display=swap">
<style>
  :root {
    --ink: #000;
    --paper: #fff;
    --accent: #e00000;
  }
  html, body {
    margin: 0;
    padding: 0;
    width: 686px;
    height: 1200px;
    overflow: hidden;
    background: var(--paper);
  }
  .card {
    position: relative;
    width: 686px;
    height: 1200px;
    background: var(--paper);
    color: var(--ink);
  }
  .frame {
    position: absolute;
    left: 25px; top: 23px;
    width: 620px; height: 1138px;
    border: 8px solid var(--ink);
  }
  .rule { position: absolute; background: var(--ink); }
  .rule-h { height: 3px; }
  .rule-v { width: 3px; }

  .row {
    position: absolute;
    left: 0; width: 686px;
    text-align: center;
    white-space: nowrap;
  }
  .at { position: absolute; text-align: center; white-space: nowrap; transform: translateX(-50%); }

  .brand-ring { position: absolute; left: 269px; top: 59px; }
  .brand-name {
    top: 212px;
    font-family: "Cinzel", serif;
    font-weight: 700;
    font-size: 45px;
    line-height: 52px;
    letter-spacing: 0.5px;
  }
  .brand-tagline {
    top: 266px;
    font-family: "Montserrat", sans-serif;
    font-weight: 700;
    font-size: 17px;
    line-height: 20px;
    letter-spacing: 9px;
    padding-left: 9px;
  }
  .headline {
    top: 305px;
    font-family: "Oswald", sans-serif;
    font-weight: 500;
    font-size: 41px;
    line-height: 52px;
    letter-spacing: 0.5px;
  }
  .label {
    font-family: "Yellowtail", cursive;
    font-size: 33px;
    line-height: 38px;
  }
  .value {
    font-family: "Pompiere", sans-serif;
    font-size: 24px;
    line-height: 26px;
    letter-spacing: 0.5px;
  }
  .web {
    font-family: "Pompiere", sans-serif;
    font-size: 19px;
    line-height: 22px;
  }
  .web .domain { color: var(--accent); }
  .address-line {
    font-family: "Yellowtail", cursive;
    font-size: 27px;
    line-height: 34px;
  }
  .signatory {
    top: 888px;
    font-family: "Yellowtail", cursive;
  }
  .signatory .person { font-size: 64px; line-height: 64px; margin-right: 14px; }
  .signatory .credentials { font-size: 21px; }
  .role {
    font-family: "Yellowtail", cursive;
    font-size: 28px;
    line-height: 34px;
  }
  .closing {
    top: 1128px;
    font-family: "Oswald", sans-serif;
    font-weight: 500;
    font-variant: small-caps;
    font-size: 38px;
    line-height: 40px;
  }
</style>
</head>
<body>
<main class="card">
  <div class="frame"></div>

  <svg class="brand-ring" width="148" height="148" viewBox="0 0 148 148" aria-hidden="true">
    <circle cx="74" cy="74" r="70" fill="none" stroke="var(--ink)" stroke-width="5"/>
  </svg>
  <div class="row brand-name">TALLOWMERE WEALTH</div>
  <div class="row brand-tagline">STRATEGIC FINANCIAL ADVICE</div>

  <div class="row headline">A REFERRAL BUILT BUSINESS</div>
  <div class="rule rule-h" style="left:128px; top:358px; width:431px;"></div>
  <div class="rule rule-v" style="left:342px; top:361px; height:68px;"></div>

  <div class="at" style="left:212px; top:366px;">
    <div class="label">Telephone</div>
    <div class="value">(07)&nbsp; 3000 1234</div>
  </div>
  <div class="at" style="left:462px; top:366px;">
    <div class="label">Fax</div>
    <div class="value">(07)&nbsp; 3000 5678</div>
  </div>

  <div class="rule rule-h" style="left:128px; top:467px; width:163px;"></div>
  <div class="rule rule-h" style="left:394px; top:467px; width:165px;"></div>
  <div class="rule rule-v" style="left:209px; top:469px; height:65px;"></div>
  <div class="rule rule-v" style="left:461px; top:469px; height:65px;"></div>
  <div class="at" style="left:343px; top:446px;">
    <div class="label">Mobile</div>
    <div class="value">0400 555 218</div>
  </div>

  <div class="at" style="left:212px; top:540px;">
    <div class="label">E-mail</div>
    <div class="web">tom@<span class="domain">brightvalefinancial</span>.com.au</div>
  </div>
  <div class="at" style="left:462px; top:540px;">
    <div class="label">Website</div>
    <div class="web">www.<span class="domain">brightvalefinancial</span>.com.au</div>
  </div>

  <div class="rule rule-h" style="left:128px; top:600px; width:431px;"></div>
  <div class="rule rule-v" style="left:341px; top:602px; height:68px;"></div>

  <div class="row label" style="top:677px;">Address</div>
  <div class="row address-line" style="top:718px;">Suite 4A, 18 Ferncliff St</div>
  <div class="row address-line" style="top:759px;">Wattle Point QLD 4000</div>
  <div class="row address-line" style="top:799px;">PO Box 1024</div>
  <div class="row address-line" style="top:840px;">Hillford QLD 4000</div>

  <div class="rule rule-h" style="left:128px; top:874px; width:431px;"></div>

  <div class="row signatory">
    <span class="person">Tom Reid</span><span class="credentials">B.Ag.Ec. Dip F.P. CFP<sup>®</sup></span>
  </div>
  <div class="row role" style="top:956px;">Managing Director</div>
  <div class="row role" style="top:999px;">Authorized Representative</div>

  <div class="row closing">Financial Peace of Mind</div>
</main>
</body>
</html>
```